Classic and neutral book cover design

We are looking for a classic and neutral book cover design to be used as the template for a series of books to be published. We are hence looking for a template that will allow us to easily change the title name for all books in this series.
The use of very few colours (black and white is welcome) and few design elements is a big bonus. As a source of inspiration we would like to ask you to view the very simple and
If you think you have a cool idea that can add a twist to the formal classic look don't hesitate. Go for it !
Work will be done for a 30 year old Sweden based cultural non-profit called VĂ©ru (www.verufoundation.example). We work with the publishing and supporting of post-modern art and literature addressing contemporary topics but are also involved in assisting projects of cultural preservation.
Target Market(s)
The audience is expected to have some form of interest in culture but could range from hobbyist readers to tenure track scholars
Industry/Entity Type
Non-Profit
Requirements
Must have
- General:
- Classic and neutral feel
- Preferably very simple and few shapes
- usage of few colours (black and white is welcome)
Information to be displayed on the cover is:
- Author
- Title
- type of work e.g. play/novel (optional)
- publishing house (in this case "Veru Publishing")
Nice to have
- ideas to prevent it from become boring are of course welcome
Should not have
- - too many colours

```html
<!DOCTYPE html>
<html lang="lv">
<head>
<meta charset="utf-8">
<title>Revidents — Veru Publishing</title>
<link href="https://fonts.googleapis.com/css2?family=Jost:wght@600;700&display=swap" rel="stylesheet">
<style>
  :root {
    --backdrop: #efeeea;
    --cover: #5a5059;
    --ink: #dcd8c6;
    --ornament: #a59e92;
  }
  html, body {
    margin: 0;
    padding: 0;
    width: 1200px;
    height: 1000px;
    overflow: hidden;
    background: var(--backdrop);
  }
  .book-cover {
    position: absolute;
    left: 260px;
    top: 68px;
    width: 682px;
    height: 860px;
    background: var(--cover);
    box-shadow: 0 2px 5px rgba(0, 0, 0, 0.25);
    font-family: "Jost", "Futura", sans-serif;
    color: var(--ink);
  }
  .cover-frame {
    position: absolute;
    inset: 0;
  }
  .author,
  .publisher {
    position: absolute;
    left: 0;
    right: 0;
    margin: 0;
    text-align: center;
    font-weight: 600;
  }
  .author {
    top: 75px;
    font-size: 22px;
    letter-spacing: 0.2px;
  }
  .title-block {
    position: absolute;
    left: 0;
    right: 0;
    top: 362px;
    text-align: center;
  }
  .title {
    margin: 0;
    font-size: 47px;
    font-weight: 700;
    line-height: 1;
    letter-spacing: 0.5px;
  }
  .work-type {
    margin: -4px 0 0;
    font-size: 17px;
    font-weight: 600;
    line-height: 1;
  }
  .publisher {
    top: 751px;
    font-size: 18px;
  }
</style>
</head>
<body>
  <main class="book-cover">
    <svg class="cover-frame" width="682" height="860" viewBox="0 0 682 860">
      <path role="img" aria-label="Chain-of-rings ornamental border"
            fill="var(--ornament)" fill-rule="evenodd"
            d="M5 5 H677 V855 H5 Z M19 19 V841 H663 V19 Z"/>
      <g fill="none" stroke="var(--ink)" stroke-width="2">
        <rect x="35" y="31" width="608" height="790"/>
        <rect x="44" y="40" width="590" height="772"/>
        <rect x="53" y="49" width="571" height="755"/>
      </g>
    </svg>
    <p class="author">Mikelis Gorodecs</p>
    <div class="title-block">
      <h1 class="title">REVIDENTS</h1>
      <p class="work-type">luga</p>
    </div>
    <p class="publisher">Veru Publishing</p>
  </main>
</body>
</html>
```